Business Card for premium dental clinic

We are a premium dental clinic based in Brasov, Romania with more than 15 year on the market, providing quality dental treatment made by a team of more specialized dentists, working with modern equipment as a solution to beautiful and healthy teeth.

Our current logo for the clinic use 2 square with colors black and gold - dr Ternisu - Lumen, using family fonts Bodoni, Myriad Pro and Segoe Print.
Depending on the printing we used some gold CMYK background or gold foil picture background or a gold gradient.
We want a business card:
- eye catching business card
- distinguished business card
- premium design
- to keep the color scheme of black and gold
- to attract the customers to spent time reading the information
- modern concept

```html
<!DOCTYPE html>
<html lang="en">
<head>
<meta charset="utf-8">
<title>Lumen Dental Clinic – Business Card</title>
<link rel="stylesheet" href="https://fonts.googleapis.com/css2?family=Montserrat:wght@400;500;600;700&family=Roboto+Condensed:wght@300;400&display=swap">
<style>
  :root {
    --backdrop: #2b2b2b;
    --card-black: #0b0b0b;
    --panel-black: #000000;
    --white: #ffffff;
    --gold: #e6bd2c;
    --gold-light: #f5d658;
    --gold-deep: #b9861c;
    --text-gold: #e8d24a;
    --rule-grey: #8a8a8a;
    --text-light: #f2f2f2;
  }
  * { margin: 0; padding: 0; box-sizing: border-box; }
  html, body { width: 1200px; height: 900px; overflow: hidden; }
  body {
    background: var(--backdrop);
    position: relative;
    font-family: "Montserrat", sans-serif;
  }

  .card {
    position: absolute;
    width: 630px;
    height: 360px;
    background: var(--card-black);
    overflow: hidden;
  }

  /* ---------- Front ---------- */
  .card-front { left: 110px; top: 50px; }
  .card-front .frame {
    position: absolute;
    left: 14px; top: 14px;
    width: 602px; height: 300px;
    border: 3px solid var(--white);
    display: flex;
  }
  .card-front .foil-panel {
    width: 46%;
    height: 100%;
    background:
      radial-gradient(circle at 30% 35%, var(--gold-light) 0%, transparent 55%),
      linear-gradient(135deg, var(--gold) 0%, var(--gold-deep) 45%, var(--gold) 70%, var(--gold-light) 100%);
    position: relative;
  }
  .card-front .name-plate {
    position: absolute;
    left: 60px; top: 108px;
    width: 290px; height: 82px;
    background: var(--white);
    display: flex;
    align-items: baseline;
    justify-content: center;
    padding-top: 10px;
    font-family: "Roboto Condensed", sans-serif;
    color: #1a1a1a;
    z-index: 2;
  }
  .name-plate .title { font-size: 28px; font-weight: 300; }
  .name-plate .surname { font-size: 52px; font-weight: 300; letter-spacing: 1px; }
  .card-front .brand-panel {
    flex: 1;
    background: var(--panel-black);
    position: relative;
  }
  .brand-panel .brand-mark {
    position: absolute;
    left: 70px; top: 70px;
    display: flex;
    align-items: center;
    gap: 12px;
  }
  .brand-mark .dot {
    width: 14px; height: 14px;
    border-radius: 50%;
    background: var(--gold);
  }
  .brand-mark .brand-name {
    font-size: 56px;
    font-weight: 500;
    color: var(--white);
  }
  .brand-panel .tagline {
    position: absolute;
    right: 22px; bottom: 22px;
    font-family: "Roboto Condensed", sans-serif;
    font-size: 30px;
    font-weight: 400;
    color: var(--white);
  }
  .card-front .gold-band {
    position: absolute;
    left: 0; bottom: 18px;
    width: 100%; height: 18px;
    background: linear-gradient(90deg, var(--gold-deep) 0%, var(--gold) 35%, var(--gold-light) 65%, var(--gold) 100%);
  }

  /* ---------- Back ---------- */
  .card-back { left: 460px; top: 490px; }
  .card-back .doctor-name {
    position: absolute;
    right: 40px; top: 42px;
    font-size: 26px;
    font-weight: 700;
    color: var(--text-gold);
  }
  .card-back .top-rule {
    position: absolute;
    left: 250px; right: 30px; top: 88px;
    height: 1px;
    background: var(--rule-grey);
  }
  .card-back .brand-block {
    position: absolute;
    left: 30px; top: 70px;
    width: 220px; height: 120px;
    background: var(--panel-black);
    display: flex;
    align-items: center;
    justify-content: center;
    gap: 10px;
  }
  .brand-block .dot {
    width: 12px; height: 12px;
    border-radius: 50%;
    background: var(--gold);
  }
  .brand-block .brand-name {
    font-size: 50px;
    font-weight: 500;
    color: var(--white);
  }
  .card-back .contact-rule {
    position: absolute;
    left: 30px; top: 210px;
    width: 300px; height: 1px;
    background: var(--rule-grey);
  }
  .card-back .contacts {
    position: absolute;
    left: 34px; top: 224px;
    list-style: none;
  }
  .contacts li {
    display: flex;
    align-items: center;
    gap: 14px;
    height: 27px;
    font-size: 17px;
    color: var(--text-light);
  }
  .contacts svg { width: 16px; height: 16px; flex: none; }
  .card-back .address {
    position: absolute;
    right: 40px; top: 160px;
    text-align: right;
    font-size: 17px;
    line-height: 1.3;
    color: var(--text-gold);
  }
</style>
</head>
<body>

  <section class="card card-front" aria-label="Business card front">
    <div class="frame">
      <div class="foil-panel" role="img" aria-label="Gold foil texture background"></div>
      <div class="brand-panel">
        <div class="brand-mark">
          <span class="dot"></span>
          <span class="brand-name">Lumen</span>
        </div>
        <div class="tagline">dental clinic</div>
      </div>
    </div>
    <div class="name-plate">
      <span class="title">dr.</span><span class="surname">Ternisu</span>
    </div>
    <div class="gold-band"></div>
  </section>

  <section class="card card-back" aria-label="Business card back">
    <div class="doctor-name">dr.Ternisu</div>
    <div class="top-rule"></div>

    <div class="brand-block">
      <span class="dot"></span>
      <span class="brand-name">Lumen</span>
    </div>

    <div class="contact-rule"></div>
    <ul class="contacts">
      <li>
        <svg viewBox="0 0 16 16" fill="none" stroke="var(--text-gold)" stroke-width="1.5" stroke-linecap="round" stroke-linejoin="round"><path d="M3 2h3l1.5 3.5-2 1.2a8 8 0 0 0 3.8 3.8l1.2-2L14 10v3a1.5 1.5 0 0 1-1.5 1.5A11.5 11.5 0 0 1 1.5 3.5 1.5 1.5 0 0 1 3 2z"/></svg>
        +00 000 417 5200
      </li>
      <li>
        <svg viewBox="0 0 16 16" fill="none" stroke="var(--text-gold)" stroke-width="1.5" stroke-linecap="round"><rect x="4" y="1.5" width="8" height="13" rx="1.5"/><line x1="7" y1="12" x2="9" y2="12"/></svg>
        +00 000 417 5200
      </li>
      <li>
        <svg viewBox="0 0 16 16" fill="none" stroke="var(--text-gold)" stroke-width="1.5" stroke-linejoin="round"><rect x="1.5" y="3.5" width="13" height="9"/><path d="M1.5 3.5 8 9l6.5-5.5"/></svg>
        info@lumendentalcare.com
      </li>
      <li>
        <svg viewBox="0 0 16 16" fill="none" stroke="var(--text-gold)" stroke-width="1.4"><circle cx="8" cy="8" r="6.5"/><ellipse cx="8" cy="8" rx="3" ry="6.5"/><line x1="1.5" y1="8" x2="14.5" y2="8"/></svg>
        www.lumendentalcare.com
      </li>
    </ul>

    <address class="address" style="font-style: normal;">
      72 Lindenfield Street<br>
      Brasov 500030
    </address>
  </section>

</body>
</html>
```